Photography business - business card design quick turn around

Create a business card design for me please. I actually need the final design back before the end of Sunday 13th May 7pm GMT. Sorry for the short notice.

Photoshop artwork template uploaded with artwork guidelines including printer profiles and other mandatory specifications. Only one side of the business card is required as the other side will be an image.

The design is required as an unflattened PSD file so that I can edit the text if I need to.

My brand colours are white and the teal you see in the logo. Occasionally I also use a dark grey on my website (I don't mind the shade of grey as appreciate grey on teal would be a different grey, to the grey I use on white on the website, so just use a shade of grey that matches). Font can be as the font for the logo or if you prefer I am open to another sans serif, easily legible font. Ideally font size will be 12+.Please do not use capital letters for text. I prefer everything to be lower case, if possible.

Thank you.

Lena

Target Market(s)

Other business owners who may refer me and families

Industry/Entity Type

Photographer

Contact Information for Business Card

Silver Kettle Photography Logo
Sub text: family portraiture, captured with love

Contact information, ideally using simple icons to represent email / website / facebook / instagram / pinterest

email: lena@silverkettlephotography.co.uk
website: silverkettlephotography.co.uk
facebook: @silverkettlephotography
pinterest: pinterest.com/silverkettlepho
instagram: @silverkettle_photography
mobile/telephone: 07713460291

If there is too much text then please drop the instagram and pinterest information.

Font styles to use
Sans Serif

Colors
33b8a4

Requirements
Must have
• Logo
• Contact details as listed above
• sub text
Nice to have
• Instagram and Pinterest contact details
• Nice to have icons to represent website / phone / facebook etc followered by the handle where relevant

```html
<!DOCTYPE html>
<html lang="en">
<head>
<meta charset="utf-8">
<title>Silver Kettle Photography — business card</title>
<link rel="stylesheet" href="https://fonts.googleapis.com/css2?family=Arimo:wght@400;600&display=swap">
<style>
  :root {
    --backdrop: #2c2c2d;
    --card-top: #ffffff;
    --card-bottom: #e6e6e7;
    --ink: #151515;
    --band: #5e6064;
    --band-light: #8d8f93;
    --rule: #7b7d81;
    --on-band: #ffffff;
    --icon: #d9dadc;
  }
  html, body {
    margin: 0;
    width: 1200px;
    height: 997px;
    overflow: hidden;
    background: var(--backdrop);
    font-family: "Arimo", Arial, sans-serif;
  }
  .card {
    position: absolute;
    left: 160px;
    top: 228px;
    width: 880px;
    height: 540px;
    border-radius: 26px;
    overflow: hidden;
    background: linear-gradient(180deg, var(--card-top) 0%, var(--card-bottom) 100%);
  }
  .brand {
    position: absolute;
    left: 110px;
    top: 150px;
    margin: 0;
    font-weight: 600;
    font-size: 38px;
    letter-spacing: 1px;
    color: var(--ink);
  }
  .rule {
    position: absolute;
    left: 0;
    width: 100%;
    background: var(--rule);
  }
  .rule--upper { top: 252px; height: 5px; background: var(--band-light); }
  .rule--mid { top: 444px; height: 4px; }
  .rule--lower { top: 494px; height: 4px; }
  .contact-band {
    position: absolute;
    left: 0;
    top: 266px;
    width: 100%;
    height: 170px;
    background: linear-gradient(180deg, var(--band) 0%, #6a6c70 100%);
    color: var(--on-band);
  }
  .contact-list, .social-list {
    position: absolute;
    margin: 0;
    padding: 0;
    list-style: none;
    font-size: 20px;
  }
  .contact-list { left: 40px; top: 58px; }
  .contact-list li, .social-list li {
    display: flex;
    align-items: center;
    height: 34px;
  }
  .contact-list svg { width: 20px; height: 20px; margin-right: 18px; fill: var(--icon); }
  .social-list { right: 36px; top: 14px; text-align: right; }
  .social-list li { justify-content: flex-end; }
  .social-mark {
    width: 14px;
    height: 14px;
    margin-left: 22px;
    border-radius: 50%;
    background: var(--icon);
  }
  .tagline {
    position: absolute;
    left: 260px;
    top: 455px;
    margin: 0;
    font-size: 24px;
    color: var(--ink);
  }
</style>
</head>
<body>
  <main class="card">
    <h1 class="brand">Silver Kettle Photography</h1>

    <div class="rule rule--upper"></div>

    <section class="contact-band" aria-label="contact details">
      <ul class="contact-list">
        <li>
          <svg viewBox="0 0 24 24" aria-hidden="true"><path d="M6.6 10.8a15 15 0 0 0 6.6 6.6l2.2-2.2c.3-.3.7-.4 1-.2 1.1.4 2.3.6 3.6.6.6 0 1 .4 1 1V20c0 .6-.4 1-1 1A17 17 0 0 1 3 4c0-.6.4-1 1-1h3.5c.6 0 1 .4 1 1 0 1.2.2 2.4.6 3.6.1.3 0 .7-.2 1z"/></svg>
          07713460291
        </li>
        <li>
          <svg viewBox="0 0 24 24" aria-hidden="true"><path d="M2 5h20v14H2zm2 2v.4l8 5 8-5V7zm0 2.8V17h16V9.8l-8 5z"/></svg>
          lena@silverkettlephotography.co.uk
        </li>
        <li>
          <svg viewBox="0 0 24 24" aria-hidden="true"><path d="M12 2a10 10 0 1 0 0 20 10 10 0 0 0 0-20zm6.9 9h-3a15 15 0 0 0-1.3-6A8 8 0 0 1 18.9 11zM12 4c.9 1.3 1.7 3.9 1.9 7h-3.8C10.3 7.9 11.1 5.3 12 4zM9.4 5a15 15 0 0 0-1.3 6h-3A8 8 0 0 1 9.4 5zm-4.3 8h3a15 15 0 0 0 1.3 6 8 8 0 0 1-4.3-6zm6.9 7c-.9-1.3-1.7-3.9-1.9-7h3.8c-.2 3.1-1 5.7-1.9 7zm2.6-1a15 15 0 0 0 1.3-6h3a8 8 0 0 1-4.3 6z"/></svg>
          silverkettlephotography.co.uk
        </li>
      </ul>

      <ul class="social-list">
        <li>silverkettlephotography<span class="social-mark"></span></li>
        <li>silverkettlepho<span class="social-mark"></span></li>
        <li>silverkettle_photography<span class="social-mark"></span></li>
      </ul>
    </section>

    <div class="rule rule--mid"></div>
    <p class="tagline">family portraiture, captured with love</p>
    <div class="rule rule--lower"></div>
  </main>
</body>
</html>
```